Marava Cove Lodge Christmas wishes 2013

We require postcards designed to mail our to our clients for Christmas. We are a SURF travel company, with a high end market and like to mail our Christmas postcards to all our guests that have stayed with us through the year. Front cover will have images and text (ie Seasons Greeting) and our logo. The back will have space for TO: name & address and postage stamp. Will also have some basic text (ie The Management & Staff at Marava Cove Lodge wish you and your family all the best for the Festive Season and New Year. We look forward to seeing you back at Marava Cove Lodge again soon etc etc). Here is link to main image https://www.filecrate-example.com/sh/qwmxrtz481plo/Vb7kRtPwqN

Target Market(s)

Our clients are mostly mature men (40-70) surfers who purchase luxury surf trips

Industry/Entity Type

Travel

Requirements
Must have
• Ocean Image (front)
Logo x 2 in same colour - Orindel & Marava Cove Lodge (front)
Text (front)
Back to be white
Space for name & address (back)
Space for postage stamp (back)
Message (back)
Website www.orindellodges-example.com (back)

```html
<!DOCTYPE html>
<html lang="en">
<head>
<meta charset="utf-8">
<title>Marava Cove Lodge – Seasons Greetings Postcard</title>
<link href="https://fonts.googleapis.com/css2?family=Signika:wght@400;600;700&family=Montserrat:wght@300;500;700&display=swap" rel="stylesheet">
<style>
  :root {
    --backdrop: #e07a2a;
    --card-white: #ffffff;
    --ink: #2a2a2a;
    --stamp-grey: #a8a8a8;
    --ocean-deep: #0b2f66;
    --ocean-mid: #1d5fae;
    --wave-light: #cfe6f4;
    --sky: #2f72c8;
    --reef: #2e6a52;
    --on-photo: #ffffff;
  }
  * { margin: 0; padding: 0; box-sizing: border-box; }
  html, body { width: 1200px; height: 1000px; overflow: hidden; }
  body { background: var(--backdrop); position: relative; font-family: "Signika", sans-serif; }

  .postcard { position: absolute; width: 563px; height: 375px; overflow: hidden; }
  .postcard--front { left: 323px; top: 58px; }
  .postcard--back { left: 325px; top: 509px; background: var(--card-white); }

  .front-photo {
    position: absolute; inset: 0;
    background:
      linear-gradient(180deg, rgba(46,106,82,0) 50%, rgba(46,106,82,0.9) 100%),
      linear-gradient(90deg, var(--ocean-deep) 0%, var(--ocean-mid) 25%, var(--wave-light) 45%, var(--ocean-mid) 62%, var(--sky) 85%, #79a9dd 100%);
  }

  .front-greeting {
    position: absolute; left: 282px; top: 33px;
    font-family: "Signika", sans-serif; font-weight: 700; font-size: 21px;
    color: var(--on-photo); letter-spacing: -0.2px;
  }

  .brand-mark {
    position: absolute;
    writing-mode: vertical-rl;
    color: var(--on-photo);
    font-family: "Montserrat", sans-serif;
    white-space: nowrap;
  }
  .brand-mark__dot {
    position: absolute; left: 32px; top: 68px;
    width: 14px; height: 14px; border-radius: 50%; background: var(--on-photo);
  }
  .brand-mark--group { left: 32px; top: 126px; font-size: 9.5px; font-weight: 500; letter-spacing: 1.6px; }
  .brand-mark--lodge { left: 78px; top: 127px; font-size: 8.6px; font-weight: 300; letter-spacing: 0.1px; }
  .brand-mark--region { left: 68px; top: 140px; font-size: 7.5px; font-weight: 300; letter-spacing: 0.5px; }
  .brand-mark__ring {
    position: absolute; left: 92px; top: 140px;
    width: 25px; height: 25px; border-radius: 50%;
    border: 2px solid var(--on-photo);
  }

  .back-message {
    position: absolute; left: 37px; top: 97px; width: 170px;
    font-size: 10.6px; font-weight: 600; line-height: 1.27; color: var(--ink);
    text-align: justify;
  }
  .back-message p + p { margin-top: 12px; }

  .back-website {
    position: absolute; left: 0; top: 261px; width: 244px; text-align: center;
    font-size: 9.5px; font-weight: 700; color: var(--ink); letter-spacing: -0.2px;
    white-space: nowrap;
  }

  .address-label {
    position: absolute; left: 243px;
    font-size: 12px; font-weight: 600; color: var(--ink);
  }
  .address-label--name { top: 95px; }
  .address-label--address { top: 126px; }

  .stamp-box {
    position: absolute; left: 452px; top: 38px; width: 69px; height: 69px;
    border: 3px solid var(--stamp-grey);
  }
</style>
</head>
<body>
  <section class="postcard postcard--front">
    <div class="front-photo" role="img" aria-label="Ocean photo: surfer riding inside a curling blue wave over a shallow green reef, mountains and clouds on the horizon"></div>
    <h1 class="front-greeting">Seasons Greetings!</h1>
    <span class="brand-mark__dot" aria-hidden="true"></span>
    <div class="brand-mark brand-mark--group">ORINDEL LODGES &amp; RESORTS</div>
    <div class="brand-mark brand-mark--lodge">maravacovelodge-example.com</div>
    <div class="brand-mark brand-mark--region">indonesia</div>
    <span class="brand-mark__ring" aria-hidden="true"></span>
  </section>

  <section class="postcard postcard--back">
    <div class="back-message">
      <p>The Management &amp; Staff at Marava Cove Lodge wish you and your family all the best for the Festive Season and New Year.</p>
      <p>We look forward to seeing you back at Marava Cove Lodge again soon!</p>
    </div>
    <div class="back-website">WWW.ORINDELLODGES-EXAMPLE.COM</div>
    <div class="address-label address-label--name">name</div>
    <div class="address-label address-label--address">address</div>
    <div class="stamp-box" aria-label="Postage stamp area"></div>
  </section>
</body>
</html>
```